Business Card Design

I already have a company logo for my company. I have a logo for the manufacturer we represent. I want a professional business card design.

```html
<!DOCTYPE html>
<html lang="en">
<head>
<meta charset="utf-8">
<title>Beacon Alert Group – Business Card</title>
<link rel="stylesheet" href="https://fonts.googleapis.com/css2?family=Montserrat:wght@400;500;700;800&display=swap">
<style>
  :root {
    --canvas-bg: #2a2d33;
    --card-black: #1b1b1d;
    --card-white: #ffffff;
    --brand-red: #e31e24;
    --text-grey: #555559;
    --text-light: #f2f2f2;
  }
  html, body {
    margin: 0;
    padding: 0;
    width: 1200px;
    height: 900px;
    overflow: hidden;
    background: var(--canvas-bg);
    font-family: "Montserrat", sans-serif;
  }
  .stage {
    position: relative;
    width: 1200px;
    height: 900px;
  }
  .card {
    position: absolute;
    left: 285px;
    width: 630px;
    height: 360px;
    border-radius: 22px;
    overflow: hidden;
    box-shadow: 0 12px 30px rgba(0,0,0,0.45);
  }
  .card--front { top: 60px; background: var(--card-white); }
  .card--back  { top: 480px; background: var(--card-black); }
  .card svg { display: block; width: 630px; height: 360px; }
  .brand-name { font-family: "Montserrat", sans-serif; font-weight: 800; letter-spacing: 1px; }
  .person-name { font-family: "Montserrat", sans-serif; font-weight: 700; fill: var(--brand-red); }
  .person-role { font-family: "Montserrat", sans-serif; font-weight: 500; fill: var(--text-grey); }
  .contact-line { font-family: "Montserrat", sans-serif; font-weight: 400; fill: var(--text-light); }
</style>
</head>
<body>
<main class="stage">

  <section class="card card--front" aria-label="Business card front">
    <svg viewBox="0 0 630 360" xmlns="http://www.w3.org/2000/svg">
      <!-- dark wave -->
      <path class="wave-dark" fill="var(--card-black)"
            d="M0,0 H34 C60,120 150,185 300,212 C450,240 560,280 630,326 V360 H0 Z"/>
      <!-- accent curves -->
      <path class="wave-red" fill="none" stroke="var(--brand-red)" stroke-width="5"
            d="M52,0 C76,110 160,168 306,196 C450,224 560,262 630,304"/>
      <path class="wave-line" fill="none" stroke="var(--card-black)" stroke-width="2"
            d="M44,0 C68,116 156,178 302,205 C448,233 558,272 630,316"/>
      <!-- edge accent -->
      <rect class="edge-band" x="612" y="222" width="18" height="62" fill="var(--brand-red)"/>

      <!-- company name -->
      <rect class="brand-mark" x="150" y="62" width="22" height="22" fill="var(--brand-red)"/>
      <text class="brand-name" x="182" y="82" font-size="24" fill="var(--brand-red)">BEACON ALERT GROUP</text>

      <!-- person -->
      <text class="person-name" x="588" y="150" font-size="26" text-anchor="end">Daniel Reyes</text>
      <text class="person-role" x="588" y="172" font-size="14" text-anchor="end">Managing Director</text>

      <!-- contact -->
      <g class="contact" font-size="14" text-anchor="end">
        <text class="contact-line" x="432" y="254">2480 Harlow Ave</text>
        <text class="contact-line" x="432" y="274">Denver, CO 80205</text>
        <text class="contact-line" x="432" y="298">502.555.0187</text>
        <text class="contact-line" x="432" y="318">info@beaconalertgroup.com</text>
        <text class="contact-line" x="432" y="338">www.beaconalertgroup.com</text>
      </g>
      <!-- icons -->
      <g class="contact-icons" fill="var(--brand-red)">
        <rect x="443" y="286" width="13" height="14" rx="3"/>
        <rect x="446" y="289" width="7" height="5" fill="var(--card-black)"/>
        <rect x="442" y="308" width="15" height="11" rx="1.5"/>
        <path d="M442,309 L449.5,315 L457,309" fill="none" stroke="var(--card-black)" stroke-width="1.5"/>
        <circle cx="449.5" cy="333" r="7.5"/>
        <path d="M442,333 H457 M449.5,325.5 C445,330 445,336 449.5,340.5 C454,336 454,330 449.5,325.5"
              fill="none" stroke="var(--card-black)" stroke-width="1.2"/>
      </g>
    </svg>
  </section>

  <section class="card card--back" aria-label="Business card back">
    <svg viewBox="0 0 630 360" xmlns="http://www.w3.org/2000/svg">
      <rect class="brand-mark" x="150" y="165" width="26" height="26" fill="var(--brand-red)"/>
      <text class="brand-name" x="188" y="189" font-size="28" fill="var(--text-light)">BEACON ALERT GROUP</text>
    </svg>
  </section>

</main>
</body>
</html>
```